Modern design company business card design

We are a design oriented construction firm. The owner is an architect and licensed General Contractor and accomplished furniture designer. We do new home construction and large scale remodeling and office design. We would like a design for our new business cards that is clean and modern, but relatable. We like the bright green color of our logo mixed with different shades of grey. We're also open to reinterpreting the logo.

Target Market(s)

Potential design clients,
Construction clients

Industry/Entity Type

Architecture

Contact Information for Business Card

Tall Maple Design | Build Inc. (optional with logo, Inc. optional)Jeffrey MorganOwner (optional)317.555.0148 cell317.431.8056 officejmorgan@greensquareinc.comwww.tallmapleinc.example

Font styles to use
Sans Serif
Other font styles liked:
• Avenir

Requirements
Nice to have
• I like designs that have some continuity between the front and back, i.e. similar layouts or graphic elements that wrap around the card. I tend to prefer horizontal over vertical, but that's not a have to. I also tend to prefer white or recycled paper.

```html
<!DOCTYPE html>
<html lang="en">
<head>
<meta charset="utf-8">
<title>Tall Maple Design | Build – Business Card</title>
<link rel="stylesheet" href="https://fonts.googleapis.com/css2?family=Nunito+Sans:ital,wght@0,300;0,400;0,700;1,400&display=swap">
<style>
  :root {
    --page: #3d3d3f;
    --paper: #ffffff;
    --grey: #8f9196;
    --grey-text: #8a8c90;
    --ink: #4a4a4c;
    --rule: #7a7a7c;
    --green-light: #c4da6a;
    --green: #7cc45a;
    --green-name: #6dbe4b;
    --green-panel: #a9d263;
  }
  * { box-sizing: border-box; margin: 0; padding: 0; }
  html, body { width: 1105px; height: 1200px; overflow: hidden; }
  body {
    background: var(--page);
    font-family: "Nunito Sans", sans-serif;
    position: relative;
  }
  .card {
    position: absolute;
    left: 196px;
    width: 720px;
    height: 412px;
    overflow: hidden;
  }
  .card--front { top: 145px; background: var(--paper); }
  .card--back  { top: 602px; background: var(--grey); }

  /* front */
  .brand {
    position: absolute; right: 36px; top: 78px;
    text-align: right; color: var(--grey-text); text-transform: uppercase;
  }
  .brand-name {
    font-size: 30px; font-weight: 400; letter-spacing: 1.5px; line-height: 1;
  }
  .brand-tagline {
    margin-top: 10px; font-size: 13px; font-weight: 400; letter-spacing: 1.4px; line-height: 1;
  }
  .person-name {
    position: absolute; left: 30px; top: 200px;
    font-size: 27px; font-weight: 700; color: var(--green-name);
    text-transform: uppercase; line-height: 1.2;
  }
  .person-role {
    position: absolute; left: 30px; top: 235px;
    font-size: 19px; font-weight: 400; color: var(--ink);
    text-transform: uppercase; line-height: 1.2;
  }
  .divider {
    position: absolute; left: 30px; top: 267px; width: 651px; height: 2px;
    background: var(--rule);
  }
  .contact-list { position: absolute; left: 30px; top: 282px; list-style: none; }
  .contact-item {
    display: flex; align-items: center; height: 28px;
    font-size: 19px; color: var(--ink);
  }
  .contact-item svg { width: 20px; height: 20px; margin-right: 11px; fill: var(--green); }
  .accent-band {
    position: absolute; left: 0; top: 392px; width: 440px; height: 20px;
    background: linear-gradient(to right, var(--green) 0%, var(--green-light) 45%, var(--green) 100%);
  }
  .web-tab {
    position: absolute; right: 0; bottom: 0; width: 306px; height: 38px;
  }
  .web-tab svg { position: absolute; inset: 0; }
  .web-tab__text {
    position: absolute; right: 36px; top: 6px;
    font-size: 20px; font-style: italic; color: var(--paper); letter-spacing: 1px;
  }

  /* back */
  .back-panel {
    position: absolute; left: 0; top: 0; width: 400px; height: 412px;
    background: var(--green-panel);
  }
  .back-name {
    position: absolute; right: 45px; top: 182px; text-align: right;
    font-size: 52px; font-weight: 400; color: var(--paper);
    text-transform: uppercase; line-height: 50px; letter-spacing: 2px;
  }
  .back-tagline {
    position: absolute; right: 45px; top: 288px; text-align: right;
    font-size: 27px; font-weight: 300; color: var(--paper);
    text-transform: uppercase; letter-spacing: 1.5px; line-height: 30px;
  }
  .back-tagline span:first-child {
    display: inline-block; border-bottom: 2px solid var(--paper); line-height: 28px;
  }
  .back-web {
    position: absolute; right: 45px; top: 358px;
    font-size: 19px; font-style: italic; color: var(--paper);
  }
</style>
</head>
<body>
  <section class="card card--front" aria-label="Business card front">
    <div class="brand">
      <p class="brand-name">Tall Maple</p>
      <p class="brand-tagline">Design | Build</p>
    </div>

    <h1 class="person-name">Dennis Holloway</h1>
    <p class="person-role">Owner</p>
    <div class="divider"></div>

    <ul class="contact-list">
      <li class="contact-item">
        <svg viewBox="0 0 24 24" aria-hidden="true"><path d="M6.6 10.8a15.1 15.1 0 0 0 6.6 6.6l2.2-2.2a1 1 0 0 1 1-.25 11.4 11.4 0 0 0 3.6.57 1 1 0 0 1 1 1V20a1 1 0 0 1-1 1A17 17 0 0 1 3 4a1 1 0 0 1 1-1h3.5a1 1 0 0 1 1 1c0 1.25.2 2.450.57 3.6a1 1 0 0 1-.25 1z"/></svg>
        317.555.0148
      </li>
      <li class="contact-item">
        <svg viewBox="0 0 24 24" aria-hidden="true"><path d="M7 1h10a2 2 0 0 1 2 2v18a2 2 0 0 1-2 2H7a2 2 0 0 1-2-2V3a2 2 0 0 1 2-2zm0 3v14h10V4zm5 15.2a1.1 1.1 0 1 0 0 2.2 1.1 1.1 0 0 0 0-2.2z"/></svg>
        317.555.0172
      </li>
      <li class="contact-item">
        <svg viewBox="0 0 24 24" aria-hidden="true"><path d="M2 6.5V19h20V6.5l-10 7zM2.5 5h19L12 11.6z"/></svg>
        dholloway@tallmapleinc.example
      </li>
    </ul>

    <div class="accent-band"></div>
    <div class="web-tab">
      <svg viewBox="0 0 306 38" width="306" height="38" aria-hidden="true">
        <polygon points="25,0 306,0 306,38 0,38" fill="var(--grey)"/>
      </svg>
      <span class="web-tab__text">tallmapleinc.example</span>
    </div>
  </section>

  <section class="card card--back" aria-label="Business card back">
    <div class="back-panel"></div>
    <p class="back-name">Tall<br>Maple</p>
    <p class="back-tagline"><span>Design</span><br><span>Build</span></p>
    <p class="back-web">www.tallmapleinc.example</p>
  </section>
</body>
</html>
```